Logo, Web and Mobile Designs for enterprise social media platform

All the details are in the attached document, please start reading the scope document first which explains what is this project about and the details about the needed deliverables, after that please read the UI_Requirements document which will detail what is expected regarding the coded web version since this is a coded contest, it is very important that you meet the UI requirements or suggest something else but we will need to agree first before working on the coded version

Good Luck

Target Market(s)

Enterprise Social Media

Industry/Entity Type

Media

Coding

Coded - Design and coding required

Number of Pages Required

5+ page

Font styles to use
Sans Serif

Requirements
Must have
• All the must haves are listed in the scope document so please check before you start

```html
<!DOCTYPE html>
<html lang="en">
<head>
<meta charset="utf-8">
<title>Collabrix – Social Media Platform</title>
<link href="https://fonts.googleapis.com/css2?family=Oswald:wght@300;400;500&family=Roboto:wght@400;500&display=swap" rel="stylesheet">
<style>
:root{
  --brand-blue:#1a8fc0;
  --accent-orange:#f7860f;
  --nav-text:#555a60;
  --header-bg:#f5f5f5;
  --panel-blue:rgba(30,152,205,.9);
  --footer-bg:#222222;
  --footer-text:#ffffff;
  --btn-text:#333333;
  --wood:#6a4c3a;
  --crowd-dark:#3a3438;
  --table-white:#ece9e7;
}
*{margin:0;padding:0;box-sizing:border-box}
html,body{width:1200px;height:861px;overflow:hidden;background:#fff}
body{font-family:"Roboto",Arial,sans-serif;position:relative}

.site-header{position:absolute;left:0;top:0;width:1200px;height:100px;background:linear-gradient(#ffffff,var(--header-bg))}
.brand{position:absolute;left:89px;top:37px;display:flex;align-items:center;gap:10px}
.brand-mark{width:22px;height:22px;background:var(--accent-orange);border-radius:50%}
.brand-name{font-family:"Oswald",sans-serif;font-weight:500;font-size:29px;color:var(--brand-blue);letter-spacing:.2px;line-height:1}

.main-nav{position:absolute;left:0;top:14px;width:1200px;height:72px}
.nav-item{position:absolute;top:0;height:72px;display:flex;align-items:center;gap:10px;font-size:12.5px;color:var(--nav-text);text-transform:uppercase;padding-top:10px}
.nav-item svg{width:16px;height:16px;fill:var(--brand-blue)}
.nav-sep{position:absolute;top:0;width:1px;height:72px;background:#ececec}
.login-btn{position:absolute;left:1036px;top:39px;width:76px;height:31px;background:linear-gradient(#fa961f,var(--accent-orange));color:#fff;font-size:14px;display:flex;align-items:center;justify-content:center;border-radius:2px;text-transform:uppercase}

.hero{position:absolute;left:0;top:100px;width:1200px;height:647px;
  background:
    radial-gradient(ellipse 120px 70px at 680px 250px,rgba(40,110,150,.55),transparent 70%),
    radial-gradient(ellipse 70px 60px at 970px 250px,rgba(160,40,50,.5),transparent 70%),
    radial-gradient(ellipse 60px 50px at 90px 230px,rgba(150,40,50,.4),transparent 70%),
    radial-gradient(ellipse 420px 120px at 300px 250px,rgba(45,40,45,.55),transparent 70%),
    radial-gradient(ellipse 420px 110px at 900px 260px,rgba(40,38,45,.5),transparent 70%),
    radial-gradient(ellipse 500px 180px at 900px 560px,rgba(250,248,246,.85),transparent 70%),
    radial-gradient(ellipse 300px 60px at 200px 550px,rgba(70,120,170,.45),transparent 70%),
    linear-gradient(180deg,var(--wood) 0%,#7a5a45 14%,#5e5250 30%,#6a6464 45%,#b9b2ae 62%,var(--table-white) 80%,#d8d2cd 100%)}
.hero-panel{position:absolute;left:83px;top:255px;width:441px;height:212px;background:var(--panel-blue)}
.hero-title{position:absolute;left:42px;top:26px;font-family:"Oswald",sans-serif;font-weight:400;font-size:41px;color:#fff;line-height:1.1;letter-spacing:-.6px;text-transform:uppercase;white-space:nowrap}
.hero-text{position:absolute;left:45px;top:80px;font-family:"Oswald",sans-serif;font-weight:300;font-size:19px;color:#fff;line-height:26px;letter-spacing:-.2px;white-space:nowrap}
.hero-btn{position:absolute;left:48px;top:147px;width:148px;height:40px;background:linear-gradient(#ffffff,#e4e4e4);color:var(--btn-text);font-family:"Oswald",sans-serif;font-size:17px;display:flex;align-items:center;justify-content:center;border-radius:3px;box-shadow:0 2px 3px rgba(0,0,0,.3);text-transform:uppercase}

.site-footer{position:absolute;left:0;top:747px;width:1200px;height:114px;background:var(--footer-bg);color:var(--footer-text)}
.footer-links{position:absolute;left:106px;top:32px;font-size:14.5px;display:flex;gap:10px}
.copyright{position:absolute;left:107px;top:62px;font-size:12.5px}
.social{position:absolute;left:964px;top:36px;display:flex;gap:8px}
.social span{width:34px;height:33px;border-radius:2px;display:flex;align-items:center;justify-content:center;box-shadow:inset 0 -3px 0 rgba(0,0,0,.15)}
.social span::after{content:"";width:12px;height:12px;border-radius:50%;background:#fff}
.social .s1{background:#29b3e8}
.social .s2{background:#d22b20}
.social .s3{background:#2d5aa0}
.social .s4{background:#1a7ac0}
</style>
</head>
<body>
<header class="site-header">
  <div class="brand"><span class="brand-mark"></span><span class="brand-name">COLLABRIX</span></div>
  <nav class="main-nav">
    <div class="nav-item" style="left:507px"><svg viewBox="0 0 16 16"><path d="M8 1 0 8h2v7h4.5v-4.5h3V15H14V8h2z"/></svg></div>
    <span class="nav-sep" style="left:547px"></span>
    <div class="nav-item" style="left:569px"><svg viewBox="0 0 16 16"><path d="M1 3h14v10H1zm1.5 1.5v.4L8 9l5.5-4.1v-.4zm0 2.2v4.8h11V6.7L8 10.8z"/></svg>Messages</div>
    <span class="nav-sep" style="left:679px"></span>
    <div class="nav-item" style="left:699px"><svg viewBox="0 0 16 16"><circle cx="5" cy="4.5" r="2.5"/><circle cx="11" cy="4.5" r="2.5"/><path d="M0 12c0-3 2-4.5 5-4.5s5 1.5 5 4.5zM8 12c0-2 .6-3.2 1.8-4 .4-.1.8-.1 1.2-.1 3 0 5 1.5 5 4.1z"/></svg>People</div>
    <span class="nav-sep" style="left:793px"></span>
    <div class="nav-item" style="left:814px"><svg viewBox="0 0 16 16"><ellipse cx="6" cy="6" rx="6" ry="4.3"/><path d="M2 9l-1 3 4-2zM13 6.5c1.8.7 3 2 3 3.5 0 1-.5 1.8-1.3 2.4l.8 2.3-3-1.6c-.5.1-1 .2-1.5.2-2 0-3.6-.9-4.3-2.2 3.5-.2 6.3-2 6.3-4.6z"/></svg>Groups</div>
    <span class="nav-sep" style="left:912px"></span>
    <div class="nav-item" style="left:928px"><svg viewBox="0 0 16 16"><path d="M1 3h14v12H1zm1.5 4v6.5h11V7zM4 1h2v3H4zm6 0h2v3h-2z"/><path d="M3.5 8.5h2v1.5h-2zm3.5 0h2v1.5H7zm3.5 0h2v1.5h-2zM3.5 11.3h2v1.5h-2zm3.5 0h2v1.5H7z"/></svg>Events</div>
    <span class="nav-sep" style="left:1016px"></span>
  </nav>
  <div class="login-btn">Login</div>
</header>

<section class="hero" role="img" aria-label="Blurred photo of a conference room with seated attendees, microphones and water jugs on white tables">
  <div class="hero-panel">
    <h1 class="hero-title">Social Media Platform</h1>
    <p class="hero-text">Lorem ipsum dolor sit amet, consectetur adipiscing<br>elit sed do eiusmod tempor incididunt</p>
    <div class="hero-btn">Get Start Now</div>
  </div>
</section>

<footer class="site-footer">
  <div class="footer-links">
    <span>Privacy Policy</span><span>|</span>
    <span>Terms of Use</span><span>|</span>
    <span>About Us</span><span>|</span>
    <span>Sitemap</span>
  </div>
  <div class="copyright">Copyright © 2015&nbsp; All Rights</div>
  <div class="social" aria-label="Social links">
    <span class="s1"></span><span class="s2"></span><span class="s3"></span><span class="s4"></span>
  </div>
</footer>
</body>
</html>
```